Membership Based Medical Practice Website

We need a functioning website for a new Membership based medical practice. There will be an enrollment fee and a monthly fee. We would like to see designs that are modern, simple. Should use neutral light colors. Examples of sites we like are www.kellanmoorclinic.com and https://fernholtcare.com/ We also have a link that when "Join Now" is clicked it will go to the signup website.

Target Market(s)

Gay Men, local population, Age group 20 to 60's.

Industry/Entity Type

Medical

Coding

Coded - Design and coding required

Number of Pages Required

5+ page

Font styles to use
Sans Serif

Colors
ffffff
cee9f5
ecf7fb
cfeae6
edf8f6
aaaaaa
e9e9e9
dbdbdb
fff3d1

Requirements
Must have
• Logo and header on every page. Clean, simple design, clear content, mobile compatible.
• Must use Wordpress
Nice to have
• Ideas should come from kellanmoorclinic.com
• Easy to read
Should not have
• Generic patient pictures, bold colors.
• Should not copy from above websites.

```html
<!DOCTYPE html>
<html lang="en">
<head>
<meta charset="utf-8">
<title>Kestrel Vale Infectious Disease Specialists</title>
<link rel="stylesheet" href="https://fonts.googleapis.com/css2?family=Montserrat:wght@400;500;600;700&family=Josefin+Sans:wght@400&display=swap">
<style>
:root{
  --white:#ffffff;
  --sky:#cee9f5;
  --sky-pale:#ecf7fb;
  --cream:#fff3d1;
  --grey-bg:#f3f3f3;
  --grey-line:#dbdbdb;
  --text:#333333;
  --text-soft:#666666;
  --hex:#bfe5f5;
  --ink:#111111;
  --footer:#262626;
}
*{margin:0;padding:0;box-sizing:border-box}
html,body{width:1200px;height:3905px;overflow:hidden}
body{position:relative;font-family:'Montserrat',sans-serif;color:var(--text);background:var(--white)}
.abs{position:absolute}
.center{text-align:center}

.topbar{left:0;top:0;width:1200px;height:62px;background:var(--cream)}
.topbar-note{left:94px;top:20px;font-size:17px;color:#222}
.social{display:flex;gap:14px}
.social span{width:24px;height:24px;border-radius:4px;background:#444;display:block}
.topbar .social{position:absolute;left:944px;top:19px}

.header{left:0;top:62px;width:1200px;height:198px;background:var(--white)}
.brand{width:320px;left:56px;top:16px;text-align:center}
.brand-mark{width:58px;height:58px;border:3px solid #d9b760;border-radius:50%;margin:0 auto 34px}
.brand-name{font-size:17px;letter-spacing:12px;color:#444;padding-left:12px}
.brand-sub{font-size:13px;color:#444;margin-top:4px;letter-spacing:.5px}
.nav{top:124px;left:531px;font-size:19px;color:#333}
.nav a{position:absolute;white-space:nowrap;color:inherit;text-decoration:none}
.join{left:960px;top:29px;width:149px;height:47px;border-radius:24px;background:var(--sky);font-size:19px;line-height:47px;text-align:center;color:#333}

.hero{left:0;top:260px;width:1200px;height:578px;background:linear-gradient(180deg,#8d8a8e 0%,#a69a94 35%,#c28a55 72%,#6e4a2a 100%)}
.hero h1{position:absolute;left:0;top:196px;width:1200px;text-align:center;font-size:46px;font-weight:700;line-height:56px;color:var(--white)}
.hero-btn{left:526px;top:349px;width:185px;height:62px;border-radius:31px;background:var(--sky);font-size:21px;line-height:62px;text-align:center;color:#222}

.expertise{left:0;top:838px;width:1200px;height:1356px;background:var(--grey-bg)}
.lead{width:1200px;top:66px;font-size:25px;color:var(--text-soft)}
.sub{width:1200px;top:115px;font-size:22px;color:#444}
.spec{width:300px;text-align:center}
.spec-pic{width:213px;height:213px;border-radius:50%;margin:0 auto}
.spec-name{font-family:'Josefin Sans',sans-serif;font-size:23px;line-height:28px;color:#444;margin-top:50px}

.perks{left:0;top:2194px;width:1200px;height:664px;background:var(--cream)}
.perks h2{position:absolute;top:56px;width:1200px;text-align:center;font-size:36px;font-weight:400;color:#333}
.perks .tag{top:121px;width:1200px;font-size:26px;color:#555}
.arrow{width:28px;height:28px;border-radius:50%;background:#555;top:320px}
.perk{width:240px;text-align:center}
.perk svg{display:block;margin:0 auto}
.perk-title{font-size:19px;line-height:22px;color:#444;margin-top:24px}
.perk-text{font-size:15px;line-height:19px;color:#444;margin:22px auto 0;width:160px}

.pricing{left:0;top:2858px;width:685px;height:552px;background:linear-gradient(180deg,var(--white) 0%,var(--sky-pale) 45%,#d3ecf6 100%)}
.pricing-photo{left:685px;top:2858px;width:515px;height:552px;background:linear-gradient(160deg,#c9c5bf 0%,#a34b2c 45%,#6a2a1b 80%,#3d2a24 100%)}
.price-h{left:110px;top:40px;font-size:26px;line-height:32px;color:#333}
.price-plan{left:110px;top:114px;font-size:24px;line-height:32px;color:#333}
.price-list{left:122px;top:212px;width:560px;list-style:none;font-size:16px;line-height:31px;color:#222}
.price-list li{position:relative;padding-left:30px}
.price-list li.dot::before{content:"";position:absolute;left:0;top:8px;width:15px;height:15px;border-radius:50%;border:2px solid #777}
.price-btn{left:112px;top:458px;width:273px;height:60px;border-radius:30px;background:var(--ink);color:var(--white);font-size:21px;line-height:60px;text-align:center}

.footer{left:0;top:3410px;width:1200px;height:495px;background:linear-gradient(180deg,#3a3a3a 0%,var(--footer) 40%,#1a1a1a 100%);color:var(--white)}
.footer .brand{left:440px;top:78px;color:var(--white)}
.footer .brand-mark{width:100px;height:100px;border-color:var(--white);margin-bottom:34px}
.footer .brand-name{font-size:22px;letter-spacing:16px;color:var(--white)}
.footer .brand-sub{font-size:19px;color:var(--white)}
.footer .nav{top:314px;left:0;color:var(--white)}
.copy{left:99px;top:427px;font-size:17px}
.footer .social{position:absolute;left:945px;top:425px}
.footer .social span{background:var(--white)}
</style>
</head>
<body>

<div class="abs topbar">
  <div class="abs topbar-note">Office hours by appointment only</div>
  <div class="social" aria-label="Social links"><span></span><span></span><span></span><span></span></div>
</div>

<header class="abs header">
  <div class="abs brand">
    <div class="brand-mark"></div>
    <div class="brand-name">KESTREL VALE</div>
    <div class="brand-sub">INFECTIOUS DISEASE SPECIALISTS</div>
  </div>
  <div class="abs join">Join us</div>
  <nav class="abs nav">
    <a style="left:0">Home</a><a style="left:99px">Specialties</a><a style="left:234px">Pricing</a><a style="left:336px">About Us</a><a style="left:461px">Faq</a><a style="left:534px">Blog</a>
  </nav>
</header>

<section class="abs hero" role="img" aria-label="Photo of friends standing arm in arm at sunset">
  <h1>Specialty medicine with Commitment,<br>Compassion and Care</h1>
  <div class="abs hero-btn">View More</div>
</section>

<section class="abs expertise">
  <p class="abs lead center">We offer comprehensive treatment of a wide variety of infectious diseases</p>
  <p class="abs sub center">Our expertise is in the following area</p>

  <div class="abs spec" style="left:115px;top:232px"><div class="spec-pic" role="img" aria-label="Photo of an HIV test form" style="background:linear-gradient(135deg,#f4f1f4,#c9c0cc)"></div><div class="spec-name">HIV/PrEP</div></div>
  <div class="abs spec" style="left:454px;top:232px"><div class="spec-pic" role="img" aria-label="Illustration of virus particles" style="background:radial-gradient(circle,#e9573a,#c43a2a 60%,#3b6f8f)"></div><div class="spec-name">Chronic Hepatitis</div></div>
  <div class="abs spec" style="left:792px;top:232px"><div class="spec-pic" role="img" aria-label="Microscope image of infected cells" style="background:radial-gradient(circle,#d9a23a,#8a5f3a 55%,#2a2e6e)"></div><div class="spec-name">Sexually transmitted<br>infections</div></div>

  <div class="abs spec" style="left:115px;top:609px"><div class="spec-pic" role="img" aria-label="Photo of capsules" style="background:linear-gradient(135deg,#e7eaec,#3cb5c4 55%,#8d9396)"></div><div class="spec-name">Pre-travel vaccinations<br>and counselling</div></div>
  <div class="abs spec" style="left:454px;top:609px"><div class="spec-pic" role="img" aria-label="Photo of a gloved hand holding a blood sample" style="background:linear-gradient(135deg,#eef2f6,#8fb4d8 55%,#3f5f8a)"></div><div class="spec-name">Infections associated<br>with medical devices</div></div>
  <div class="abs spec" style="left:792px;top:609px"><div class="spec-pic" role="img" aria-label="Image of a joint highlighted in red" style="background:linear-gradient(90deg,#5a5a5a,#c93030 55%,#6a6a6a)"></div><div class="spec-name">Bone and Joint<br>infections</div></div>

  <div class="abs spec" style="left:115px;top:976px"><div class="spec-pic" role="img" aria-label="Photo of a hand" style="background:radial-gradient(circle,#e4b49a,#f5e6dc 75%)"></div><div class="spec-name">Postsurgical<br>infections</div></div>
  <div class="abs spec" style="left:454px;top:976px"><div class="spec-pic" role="img" aria-label="Photo of a skin wound" style="background:radial-gradient(circle,#b07a5a,#d8b79a 55%,#3a3a3a)"></div><div class="spec-name">Diabetes related<br>infections</div></div>
  <div class="abs spec" style="left:792px;top:976px"><div class="spec-pic" role="img" aria-label="Microscope image of bacteria" style="background:linear-gradient(135deg,#c9735a,#e79a7a 50%,#6a3a3a)"></div><div class="spec-name">Tuberculosis</div></div>
</section>

<section class="abs perks">
  <h2>Less wait, more personal</h2>
  <p class="abs tag center">We are not your traditional doctor's office</p>
  <div class="abs arrow" style="left:41px"></div>
  <div class="abs arrow" style="left:1131px"></div>

  <div class="abs perk" style="left:104px;top:221px">
    <svg width="198" height="172" viewBox="0 0 198 172"><polygon points="49,0 149,0 198,86 149,172 49,172 0,86" fill="var(--hex)"/><circle cx="99" cy="86" r="38" fill="none" stroke="#fff" stroke-width="4"/><text x="99" y="102" text-anchor="middle" font-size="44" fill="#fff" font-family="Montserrat,sans-serif">$</text></svg>
    <div class="perk-title">Straight forward<br>Pricing</div>
    <div class="perk-text">We charge all our patients the same low rate - no surprises.</div>
  </div>
  <div class="abs perk" style="left:367px;top:221px">
    <svg width="198" height="172" viewBox="0 0 198 172"><polygon points="49,0 149,0 198,86 149,172 49,172 0,86" fill="var(--hex)"/><rect x="62" y="52" width="74" height="66" rx="6" fill="none" stroke="#fff" stroke-width="4"/><line x1="62" y1="72" x2="136" y2="72" stroke="#fff" stroke-width="4"/><line x1="80" y1="44" x2="80" y2="58" stroke="#fff" stroke-width="4"/><line x1="118" y1="44" x2="118" y2="58" stroke="#fff" stroke-width="4"/><g fill="#fff"><circle cx="80" cy="88" r="4"/><circle cx="99" cy="88" r="4"/><circle cx="118" cy="88" r="4"/><circle cx="80" cy="104" r="4"/><circle cx="99" cy="104" r="4"/></g></svg>
    <div class="perk-title">Available when<br>you are</div>
    <div class="perk-text">New patient appointments are available within 1 week.</div>
  </div>
  <div class="abs perk" style="left:611px;top:221px">
    <svg width="198" height="172" viewBox="0 0 198 172"><polygon points="49,0 149,0 198,86 149,172 49,172 0,86" fill="var(--hex)"/><path d="M99 58 Q80 48 60 52 V120 Q80 116 99 126 Q118 116 138 120 V52 Q118 48 99 58 Z M99 58 V126" fill="none" stroke="#fff" stroke-width="4"/></svg>
    <div class="perk-title">Hassle-free<br>booking</div>
    <div class="perk-text">Schedule your appointment online at your convenience - no need to call during business hours.</div>
  </div>
  <div class="abs perk" style="left:861px;top:221px">
    <svg width="198" height="172" viewBox="0 0 198 172"><polygon points="49,0 149,0 198,86 149,172 49,172 0,86" fill="var(--hex)"/><path d="M99 108 L74 84 Q64 72 74 62 Q86 52 99 66 Q112 52 124 62 Q134 72 124 84 Z" fill="none" stroke="#fff" stroke-width="4"/><path d="M56 110 Q72 100 88 120 M142 110 Q126 100 110 120" fill="none" stroke="#fff" stroke-width="4"/></svg>
    <div class="perk-title">Devoted<br>care</div>
    <div class="perk-text">We schedule enough time at each visit to make sure all of your questions are answered.</div>
  </div>
</section>

<section class="abs pricing">
  <p class="abs price-h">Our pricing is simple, transparent<br>and affordable.</p>
  <p class="abs price-plan">Membership Plan $80/mo, plus a one-time<br>$99 enrollment fee.</p>
  <ul class="abs price-list">
    <li>Includes all appointments, no co-pay</li>
    <li class="dot">Relaxed, unrushed visits</li>
    <li class="dot">Direct communication with your doctor via phone, email, video chat 24/7</li>
    <li class="dot">Convenient online scheduling (no need to call during business hours)</li>
    <li class="dot">Wholesale price for labs and medications</li>
  </ul>
  <div class="abs price-btn">Learn more about us</div>
</section>
<div class="abs pricing-photo" role="img" aria-label="Photo of a white enamel camping mug held outdoors"></div>

<footer class="abs footer">
  <div class="abs brand">
    <div class="brand-mark"></div>
    <div class="brand-name">KESTREL VALE</div>
    <div class="brand-sub">INFECTIOUS DISEASE SPECIALISTS</div>
  </div>
  <nav class="abs nav">
    <a style="left:342px">Home</a><a style="left:429px">Specialties</a><a style="left:557px">Pricing</a><a style="left:653px">About Us</a><a style="left:766px">Faq</a><a style="left:829px">Blog</a>
  </nav>
  <div class="abs copy">2019 © Copyrights Kestrel Vale Infectious Disease Specialists</div>
  <div class="social" aria-label="Social links"><span></span><span></span><span></span><span></span></div>
</footer>

</body>
</html>
```